Business Cards Design for the electrical wholesaler: clean bold dynamic :)

We need a business card design that would follow our latest brand guidelines. As an electrical wholesaler we want to bring a fresh look and feel into the industry. The design should be clean bold and dynamic. It should come alive with the renewed energy of our green colour. Our grey colour should keep things balanced and complement the notion of maturity and responsibility. We employ Lato as a corporate font however are not bound by this font and we’re open to interpretation here.

Target Market(s)

Electrical contractors

Industry/Entity Type

Business

Contact Information for Business Card

Logo
Name & Surname: Halyna Dorosh
Job Title: Director of Marketing
Email: halya.dorosh@quillmail.example
Cell phone: XXX.XXX.XXXX
Address: 20517 - 87 Ave. Edmonton, AB, Canada. T6K 4N8
Business Phone: 780.555.0184
Website: www.brovix.example

Font styles to use
Other font styles liked:
• Lato

Requirements
Must have
• Logo & website
Nice to have
• Brand elements - some of them you may find in the attached Brand Guidelines (e.g. three lines on the background signifying "W")

```html
<!DOCTYPE html>
<html lang="en">
<head>
<meta charset="utf-8">
<title>Brovix Business Cards</title>
<link rel="stylesheet" href="https://fonts.googleapis.com/css2?family=Lato:wght@400;700;900&display=swap">
<style>
  :root {
    --brand-green: #8bc23f;
    --brand-green-dark: #6f9f2c;
    --brand-grey: #4b4c50;
    --ink: #1f1f21;
    --paper: #ffffff;
    --stage: #3a3a3c;
  }
  * { margin: 0; padding: 0; box-sizing: border-box; }
  html, body { width: 1200px; height: 900px; overflow: hidden; }
  body {
    background: var(--stage);
    font-family: "Lato", Arial, sans-serif;
    position: relative;
  }
  .card {
    position: absolute;
    width: 520px;
    height: 300px;
    top: 300px;
    overflow: hidden;
    box-shadow: 0 10px 30px rgba(0,0,0,.35);
  }
  .card--front { left: 50px; background: var(--paper); }
  .card--back { left: 630px; background: var(--brand-green); }

  /* front */
  .corner-tab {
    position: absolute; left: 0; top: 0;
    width: 64px; height: 28px;
    background: var(--brand-green);
    border-bottom-right-radius: 28px;
  }
  .wordmark { position: absolute; display: flex; flex-direction: column; }
  .wordmark__row { display: flex; align-items: center; gap: 10px; }
  .wordmark__square { background: var(--brand-grey); }
  .wordmark__name { color: var(--brand-grey); font-weight: 900; line-height: 1; }
  .wordmark__tagline {
    color: var(--brand-grey); font-weight: 700;
    text-transform: uppercase; letter-spacing: .18em;
  }
  .card--front .wordmark { left: 36px; top: 42px; }
  .card--front .wordmark__square { width: 34px; height: 34px; }
  .card--front .wordmark__name { font-size: 44px; }
  .card--front .wordmark__tagline { font-size: 8px; margin: 4px 0 0 44px; }

  .address {
    position: absolute; left: 30px; top: 140px;
    font-size: 12px; line-height: 1.35; color: var(--ink);
  }
  .person { position: absolute; right: 36px; top: 112px; text-align: right; }
  .person__name { font-size: 20px; font-weight: 700; color: var(--brand-grey); }
  .person__first { color: var(--brand-green); }
  .person__title { font-size: 12px; color: var(--ink); margin-top: 2px; }

  .contacts {
    position: absolute; right: 36px; top: 166px;
    list-style: none; display: flex; flex-direction: column; gap: 5px;
  }
  .contacts__item {
    display: flex; align-items: center; justify-content: flex-end; gap: 8px;
    font-size: 13px; color: var(--ink);
  }
  .contacts__icon {
    width: 17px; height: 17px; background: var(--brand-green);
    display: flex; align-items: center; justify-content: center;
  }
  .contacts__icon svg { width: 11px; height: 11px; }

  .base-band--green {
    position: absolute; left: 0; bottom: 0;
    width: 170px; height: 14px; background: var(--brand-green);
  }
  .base-band--grey {
    position: absolute; left: 150px; bottom: 0; right: 0;
    height: 30px; background: var(--brand-grey);
    border-top-left-radius: 30px;
  }
  .side-tab {
    position: absolute; right: 0; bottom: 20px;
    width: 34px; height: 52px; background: var(--brand-grey);
    border-top-left-radius: 18px;
  }

  /* back */
  .card--back .wordmark { left: 50%; top: 92px; transform: translateX(-50%); }
  .card--back .wordmark__square { width: 52px; height: 52px; }
  .card--back .wordmark__name { font-size: 72px; }
  .card--back .wordmark__tagline { font-size: 11px; margin: 6px 0 0 64px; }
  .back-url {
    position: absolute; left: 70px; top: 228px;
    font-size: 11px; color: var(--ink);
  }
</style>
</head>
<body>

<section class="card card--front" aria-label="Business card front">
  <div class="corner-tab"></div>
  <div class="wordmark">
    <div class="wordmark__row">
      <span class="wordmark__square"></span>
      <span class="wordmark__name">Brovix</span>
    </div>
    <span class="wordmark__tagline">Electrical Wholesalers</span>
  </div>

  <p class="address">20517 - 87 Ave. Edmonton, AB,<br>Canada. T6K 4N8</p>

  <div class="person">
    <p class="person__name"><span class="person__first">Halyna</span> Dorosh</p>
    <p class="person__title">Director of Marketing</p>
  </div>

  <ul class="contacts">
    <li class="contacts__item">780.555.0127
      <span class="contacts__icon"><svg viewBox="0 0 12 12"><path d="M3 1l2 2.5-1 1.2c.6 1.3 1.5 2.2 2.8 2.8l1.2-1 2.5 2-1.2 1.8C5 10.2 1.8 7 1.2 2.2z" fill="#fff"/></svg></span>
    </li>
    <li class="contacts__item">780.555.0184
      <span class="contacts__icon"><svg viewBox="0 0 12 12"><rect x="3" y="1" width="6" height="10" rx="1" fill="none" stroke="#fff" stroke-width="1.4"/><circle cx="6" cy="9" r=".8" fill="#fff"/></svg></span>
    </li>
    <li class="contacts__item">halya.dorosh@quillmail.example
      <span class="contacts__icon"><svg viewBox="0 0 12 12"><rect x="1" y="2.5" width="10" height="7" fill="none" stroke="#fff" stroke-width="1.2"/><path d="M1 2.5l5 4 5-4" fill="none" stroke="#fff" stroke-width="1.2"/></svg></span>
    </li>
    <li class="contacts__item">www.brovix.example
      <span class="contacts__icon"><svg viewBox="0 0 12 12"><circle cx="6" cy="6" r="4.6" fill="none" stroke="#fff" stroke-width="1.2"/><ellipse cx="6" cy="6" rx="2" ry="4.6" fill="none" stroke="#fff" stroke-width="1"/><path d="M1.4 6h9.2" stroke="#fff" stroke-width="1"/></svg></span>
    </li>
  </ul>

  <div class="base-band--green"></div>
  <div class="base-band--grey"></div>
  <div class="side-tab"></div>
</section>

<section class="card card--back" aria-label="Business card back">
  <div class="wordmark">
    <div class="wordmark__row">
      <span class="wordmark__square"></span>
      <span class="wordmark__name">Brovix</span>
    </div>
    <span class="wordmark__tagline">Electrical Wholesalers</span>
  </div>
  <p class="back-url">www.brovix.example</p>
</section>

</body>
</html>
```